Q7 Landing Page

We are looking for a creative landing page & a autosignature for our email.
The launchpage will be featuring a dripmeadow provided "widget"
All instructions are in the uploaded ZIP File
**Please note that we require the landing page back complete ready to be uploaded without having to do any modifications**
Reason: Awaiting some further submissions...

```html
<!DOCTYPE html>
<html lang="en">
<head>
<meta charset="utf-8">
<title>Q7-MEDIA – Mobile Solutions for a Connected World</title>
<link rel="stylesheet" href="https://fonts.googleapis.com/css2?family=Bebas+Neue&family=Open+Sans:wght@300;400&family=Oswald:wght@500&display=swap">
<style>
  :root {
    --bg: #262626;
    --bg-band: #1d1d1d;
    --panel: #3a3a3a;
    --green: #5aab3a;
    --green-soft: #a9c45c;
    --text: #f2f2f2;
    --text-muted: #c9c9c9;
    --dots: #8a8a8a;
    --white: #ffffff;
  }
  * { margin: 0; padding: 0; box-sizing: border-box; }
  html, body { width: 1200px; height: 900px; overflow: hidden; }
  body {
    position: relative;
    background: var(--bg);
    font-family: "Open Sans", Arial, sans-serif;
    color: var(--text);
  }
  .brand { position: absolute; left: 68px; top: 22px; display: flex; align-items: flex-start; }
  .brand-square { width: 92px; height: 92px; background: var(--green); margin-top: 22px; }
  .brand-text { position: absolute; left: 113px; top: 22px; white-space: nowrap; }
  .brand-name { font-family: "Bebas Neue", Impact, sans-serif; font-size: 66px; line-height: 66px; color: var(--white); letter-spacing: 1px; }
  .brand-tagline { font-family: "Oswald", Arial, sans-serif; font-weight: 500; font-size: 17px; color: var(--white); margin-top: 10px; letter-spacing: 0; }
  .brand-rule { position: absolute; left: 181px; top: 144px; width: 952px; height: 3px; background: var(--green); }

  .device-visual {
    position: absolute; left: 70px; top: 232px; width: 332px; height: 543px;
    background: linear-gradient(180deg, #f4f4f4 0%, #dcdcdc 70%, #3a3a3a 100%);
    border-radius: 34px 34px 0 0;
  }

  .intro { position: absolute; left: 443px; top: 258px; width: 300px; }
  .intro h1 { font-weight: 300; font-size: 31px; line-height: 44px; color: var(--text); }
  .apps-callout {
    position: absolute; left: 443px; top: 358px; width: 273px; height: 45px;
    background: var(--white); border-radius: 3px;
    display: flex; align-items: center; justify-content: center; gap: 10px;
    color: var(--green); font-size: 19px;
  }
  .apps-callout::after {
    content: ""; position: absolute; left: 127px; bottom: -11px;
    border-left: 11px solid transparent; border-right: 11px solid transparent; border-top: 11px solid var(--white);
  }
  .apps-icon { width: 32px; height: 32px; background: linear-gradient(135deg, #d9a75c, #8c6b3a); border-radius: 3px; }
  .app-list { position: absolute; left: 443px; top: 430px; width: 273px; list-style: none; }
  .app-list li {
    height: 54px; padding-top: 14px; padding-left: 13px;
    border-bottom: 2px dotted var(--dots);
    font-size: 16px; text-transform: uppercase;
  }
  .app-list li::before { content: "•"; margin-right: 12px; }
  .cta-line { position: absolute; left: 441px; top: 640px; font-size: 21px; color: var(--green-soft); }

  .signup {
    position: absolute; left: 816px; top: 267px; width: 316px; height: 204px;
    background: var(--panel); border-radius: 3px; box-shadow: 0 2px 6px rgba(0,0,0,.5);
  }
  .signup p { position: absolute; left: 23px; top: 24px; font-size: 13.5px; line-height: 23px; color: var(--text); }
  .signup-field {
    position: absolute; left: 20px; top: 94px; width: 229px; height: 32px;
    background: var(--white); border: 1px solid #cfcfcf; border-radius: 2px;
    padding-left: 9px; line-height: 30px; font-size: 13px; color: #8a8a8a;
  }
  .signup-go {
    position: absolute; left: 255px; top: 94px; width: 46px; height: 32px;
    background: var(--green); color: var(--white); font-size: 17px; text-align: center; line-height: 32px; border-radius: 2px;
  }
  .signup-powered { position: absolute; left: 0; right: 0; top: 152px; text-align: center; font-size: 13px; color: var(--text-muted); }
  .signup-powered strong { font-weight: 400; font-size: 19px; color: #bdbdbd; margin-left: 8px; vertical-align: -1px; }

  .platforms-visual {
    position: absolute; left: 858px; top: 500px; width: 246px; height: 168px;
    background: radial-gradient(ellipse at center, #e8e8e8 0%, #9a9a9a 55%, rgba(38,38,38,0) 75%);
  }

  .social-band {
    position: absolute; left: 0; top: 719px; width: 1200px; height: 64px;
    background: var(--bg-band); border-top: 1px solid #2f2f2f; border-bottom: 1px solid #2f2f2f;
  }
  .social-band span { position: absolute; left: 827px; top: 22px; font-size: 14px; color: var(--text); }
  .social-links { position: absolute; left: 947px; top: 16px; display: flex; gap: 7px; }
  .social-links i { display: block; width: 30px; height: 30px; border-radius: 50%; background: var(--white); }

  .site-nav { position: absolute; left: 0; right: 0; top: 812px; text-align: center; font-size: 12px; color: var(--text-muted); }
  .site-nav a { color: var(--text-muted); text-decoration: none; margin: 0 9px; }
  .copyright { position: absolute; left: 0; right: 0; top: 846px; text-align: center; font-size: 12px; color: var(--text-muted); }
</style>
</head>
<body>
  <header class="brand">
    <div class="brand-square"></div>
    <div class="brand-text">
      <div class="brand-name">Q7-MEDIA</div>
      <div class="brand-tagline">MOBILE SOLUTIONS FOR A CONNECTED WORLD</div>
    </div>
  </header>
  <div class="brand-rule"></div>

  <div class="device-visual" role="img" aria-label="Two white smartphones, front and back, showing the Q7-MEDIA app screen"></div>

  <section class="intro">
    <h1>Transferring the Web into your Pocket</h1>
  </section>
  <div class="apps-callout"><span class="apps-icon" role="img" aria-label="Open cardboard box icon"></span>Instant Apps for :</div>
  <ul class="app-list">
    <li>Industry</li>
    <li>Product Launches</li>
    <li>Viral Marketing Campaigns</li>
  </ul>
  <p class="cta-line">For Mobile Solutions, come talk to us !</p>

  <aside class="signup">
    <p>Freedom.Delivered. Want to get mobile?<br>Let's have a talk</p>
    <div class="signup-field">email@address.com</div>
    <div class="signup-go">Go</div>
    <div class="signup-powered">Powered by <strong>dripmeadow</strong></div>
  </aside>

  <div class="platforms-visual" role="img" aria-label="Scattered cards of mobile platforms with a phone and a tablet"></div>

  <div class="social-band">
    <span>Connect with us :</span>
    <div class="social-links"><i></i><i></i><i></i><i></i><i></i></div>
  </div>

  <nav class="site-nav">
    <a href="#">Home</a>|<a href="#">About us</a>|<a href="#">Services</a>|<a href="#">Contact us</a>
  </nav>
  <p class="copyright">Copyright © 2012 www.q7-media.com &nbsp; All rights reserved.</p>
</body>
</html>
```